Redesign current business card for food company

i would like to redesign my business card. our company is food company, our product range from chips, juices, milk and etc (mostly dried food stuff).
I want o keep same logo but , the rest is open to new design.
you can check at our website about our company www.orvelpantry.com

Target Market(s)

most of food company

Industry/Entity Type

Business

Contact Information for Business Card

I want to keep more to blue color...

Colors
3176b5
abd036

Requirements
Must have
• our old logo
Nice to have
• we do not mind to have nice material on bus card in order to accomplish nice design. for example: using spot uv, embossed and etc.

```html
<!DOCTYPE html>
<html lang="en">
<head>
<meta charset="utf-8">
<title>Orvel Enterprises Corp. — Business Card</title>
<link rel="stylesheet" href="https://fonts.googleapis.com/css2?family=Nunito:wght@700&family=Open+Sans:wght@400;600&display=swap">
<style>
  :root {
    --bg: #e9e6e1;
    --paper: #f7f7f7;
    --ink: #1e1e24;
    --royal: #3b3fb3;
    --indigo: #2f2f9e;
    --brand-blue: #3176b5;
    --cyan: #1cc3d6;
    --white: #ffffff;
  }
  * { margin: 0; padding: 0; box-sizing: border-box; }
  html, body { width: 1200px; height: 780px; overflow: hidden; }
  body {
    background: var(--bg);
    display: flex;
    align-items: center;
    justify-content: center;
    gap: 60px;
    font-family: "Open Sans", Arial, sans-serif;
  }
  .card {
    position: relative;
    width: 520px;
    height: 297px;
    border-radius: 16px;
    overflow: hidden;
    box-shadow: 0 8px 24px rgba(0,0,0,.18);
  }
  .card-front { background: var(--paper); }
  .front-swoosh { position: absolute; inset: 0; width: 100%; height: 100%; }

  .company-name {
    position: absolute;
    top: 26px;
    right: 210px;
    font-size: 16px;
    color: var(--ink);
    letter-spacing: .2px;
    white-space: nowrap;
  }
  .brand {
    position: absolute;
    top: 100px;
    left: 58px;
  }
  .brand-name {
    font-family: "Nunito", Arial, sans-serif;
    font-weight: 700;
    font-size: 76px;
    line-height: 1;
    color: var(--brand-blue);
    letter-spacing: -1px;
  }
  .holder {
    position: absolute;
    left: 52px;
    bottom: 34px;
  }
  .holder-name {
    font-size: 19px;
    color: var(--royal);
    line-height: 1.1;
  }
  .holder-title {
    font-size: 13px;
    color: var(--ink);
  }

  .contact {
    position: absolute;
    top: 30px;
    right: 22px;
    text-align: right;
    color: var(--white);
    font-size: 12.5px;
    line-height: 1.45;
  }
  .contact-address { margin-bottom: 8px; }
  .contact-row {
    display: flex;
    justify-content: flex-end;
    align-items: center;
    gap: 7px;
  }
  .contact-icon {
    width: 13px; height: 13px;
    flex: none;
  }
  .card-back {
    background: radial-gradient(ellipse at 48% 52%, var(--cyan) 0%, #2a8fcf 38%, var(--royal) 78%, var(--indigo) 100%);
    display: flex;
    align-items: center;
    justify-content: center;
  }
  .back-brand {
    font-family: "Nunito", Arial, sans-serif;
    font-weight: 700;
    font-size: 104px;
    color: var(--white);
    letter-spacing: -1px;
    line-height: 1;
  }
</style>
</head>
<body>

  <section class="card card-front" aria-label="Business card front">
    <svg class="front-swoosh" viewBox="0 0 520 297" aria-hidden="true">
      <defs>
        <linearGradient id="panelFill" x1="0" y1="0" x2="1" y2="0.3">
          <stop offset="0" stop-color="#1cc3d6"/>
          <stop offset="0.45" stop-color="#3a62c4"/>
          <stop offset="1" stop-color="#3b3fb3"/>
        </linearGradient>
        <linearGradient id="waveFill" x1="0" y1="1" x2="1" y2="0">
          <stop offset="0" stop-color="#3b3fb3"/>
          <stop offset="1" stop-color="#1cc3d6"/>
        </linearGradient>
      </defs>
      <path d="M355,0 C320,70 335,170 255,230 C225,252 200,275 188,297 L520,297 L520,0 Z" fill="url(#panelFill)"/>
      <path d="M338,8 C305,80 318,170 240,228 C205,254 175,276 165,297 L178,297 C196,268 228,250 258,226 C330,168 312,80 350,4 Z" fill="url(#waveFill)"/>
      <path d="M296,140 C300,205 245,250 150,297 L168,297 C260,255 312,210 296,140 Z" fill="#111"/>
    </svg>

    <p class="company-name">Orvel Enterprises Corp.</p>

    <div class="brand">
      <span class="brand-name">orvel</span>
    </div>

    <div class="holder">
      <p class="holder-name">Marcus Hollbrook</p>
      <p class="holder-title">President</p>
    </div>

    <div class="contact">
      <p class="contact-address">2480 W. 5th St<br>Fairlane, CA 90412</p>
      <p class="contact-row">555-214-3080
        <svg class="contact-icon" viewBox="0 0 16 16" aria-label="Phone"><rect width="16" height="16" rx="3" fill="#fff"/><path d="M5 3.5l2 2-1 1.3c.7 1.4 1.8 2.5 3.2 3.2l1.3-1 2 2-1.2 1.5C7.6 12.3 3.7 8.4 3.5 4.7z" fill="#3b3fb3"/></svg>
      </p>
      <p class="contact-row">555-214-3091
        <svg class="contact-icon" viewBox="0 0 16 16" aria-label="Fax"><rect width="16" height="16" rx="3" fill="#fff"/><rect x="4" y="3" width="8" height="4" fill="#3b3fb3"/><rect x="3" y="8" width="10" height="5" rx="1" fill="#3b3fb3"/></svg>
      </p>
      <p class="contact-row">555 318 4472
        <svg class="contact-icon" viewBox="0 0 16 16" aria-label="Mobile"><rect width="16" height="16" rx="3" fill="#fff"/><rect x="5" y="2.5" width="6" height="11" rx="1.2" fill="#3b3fb3"/><rect x="6" y="4" width="4" height="6.5" fill="#fff"/></svg>
      </p>
      <p class="contact-row">marcus@orvelpantry.com
        <svg class="contact-icon" viewBox="0 0 16 16" aria-label="Email"><rect width="16" height="16" rx="3" fill="#fff"/><rect x="3" y="4.5" width="10" height="7" fill="#3b3fb3"/><path d="M3 4.5l5 4 5-4" fill="none" stroke="#fff" stroke-width="1.1"/></svg>
      </p>
    </div>
  </section>

  <section class="card card-back" aria-label="Business card back">
    <span class="back-brand">orvel</span>
  </section>

</body>
</html>
```